Natural Supplement Co Needs Label Makeover

Our company's success began with our main product, an amino acid blend that aids in fat metabolism, called Vantorel. Since then we continue to expand the product line that now includes a detox called Vantopurge, and probiotic called Vantoflora, as well as 3 others, for a total of 6 products/ labels.
Our original design/logo had more of an 'old-timey' feel (see attached 2-product photo). We are looking for a fresh label design update for the product line which reflects the range of supplements as cohesive and individual parts of an overall health plan/strategy (see attached 'Logo Update Test' as just one idea we had in-house, you need not consider it as a starting point).

Target Market(s)

women 25-45

Industry/Entity Type

Health And Wellness

Requirements
Must have
• consistent theme with confident look
Nice to have
• Each product (ie. "Vantorel") has a few-word descriptor: ("Fat-Burning Amino Acids") that should be planned on including as part of each label.
Should not have
• NO 'streamlined' or graphic interpretations of the human body, or figurative image

```html
<!DOCTYPE html>
<html lang="en">
<head>
<meta charset="utf-8">
<title>Vantorel Label</title>
<link rel="stylesheet" href="https://fonts.googleapis.com/css2?family=Arvo:wght@400;700&family=Signika:wght@600&family=Roboto+Condensed:wght@400&display=swap">
<style>
  :root {
    --backdrop: #ececec;
    --label-white: #ffffff;
    --leaf-green: #34b04a;
    --band-yellow: #f2ea2e;
    --band-yellow-light: #f7f27a;
    --ink-dark: #2e2e2e;
    --ink-grey: #555555;
    --rule-white: rgba(255, 255, 255, 0.85);
  }
  html, body {
    margin: 0;
    padding: 0;
    width: 960px;
    height: 1200px;
    overflow: hidden;
    background: var(--backdrop);
  }
  .label {
    position: absolute;
    left: 130px;
    top: 100px;
    width: 700px;
    height: 1000px;
    background: var(--label-white);
    box-shadow: 0 4px 18px rgba(0, 0, 0, 0.08);
  }
  .label__panel {
    position: absolute;
    left: 60px;
    top: 0;
    width: 587px;
    height: 760px;
    background: var(--leaf-green);
  }
  .label__band {
    position: absolute;
    left: 10px;
    top: 110px;
    width: 680px;
    height: 162px;
    background: linear-gradient(180deg, var(--band-yellow-light) 0%, var(--band-yellow) 45%, var(--band-yellow) 100%);
    display: flex;
    align-items: center;
    justify-content: center;
  }
  .label__descriptor {
    font-family: "Arvo", serif;
    font-size: 72px;
    color: var(--ink-dark);
    letter-spacing: 0.5px;
  }
  .label__brand {
    position: absolute;
    left: 60px;
    width: 587px;
    top: 340px;
    text-align: center;
    font-family: "Signika", sans-serif;
    font-weight: 600;
    font-size: 140px;
    line-height: 1;
    color: var(--label-white);
  }
  .label__rule {
    position: absolute;
    left: 100px;
    width: 505px;
    height: 2px;
    background: var(--rule-white);
  }
  .label__rule--top { top: 580px; }
  .label__rule--bottom { top: 704px; }
  .label__category {
    position: absolute;
    left: 60px;
    width: 587px;
    top: 612px;
    text-align: center;
    font-family: "Arvo", serif;
    font-size: 58px;
    color: var(--label-white);
    letter-spacing: 1px;
  }
  .label__claim {
    position: absolute;
    left: 0;
    width: 700px;
    top: 788px;
    text-align: center;
    font-family: "Arvo", serif;
    font-weight: 700;
    font-size: 47px;
    color: var(--ink-dark);
    letter-spacing: -0.5px;
  }
  .label__volume {
    position: absolute;
    left: 0;
    width: 700px;
    top: 925px;
    text-align: center;
    font-family: "Roboto Condensed", sans-serif;
    font-size: 30px;
    color: var(--ink-grey);
  }
</style>
</head>
<body>
  <div class="label">
    <div class="label__panel"></div>
    <div class="label__band">
      <span class="label__descriptor">Fat Burning</span>
    </div>
    <div class="label__brand">Vantorel</div>
    <div class="label__rule label__rule--top"></div>
    <div class="label__category">AMINO ACIDS</div>
    <div class="label__rule label__rule--bottom"></div>
    <div class="label__claim">ALL NATURAL SUPPLEMENT</div>
    <div class="label__volume">1 FL. OZ (30 ml)</div>
  </div>
</body>
</html>
```